BUSINESS CARD DESIGN

NAME- DALE VORSKIN
PHONE NUMER - 555- 714-9082
EMAIL- OFFICE@TRV-GROUNDMAKRZ.COM
BACK OF CARD- SPEACIALIZES IN LAND CLEARING, FORESTRY MUCLHING AND EXCAVATION

Contact Information for Business Card

NAME- DALE VORSKIN PHONE NUMER - 555- 714-9082 EMAIL- OFFICE@TRV-GROUNDMAKRZ.COM BACK OF CARD- SPEACIALIZES IN LAND CLEARING , MUCLHING AND EXCAVATION

```html
<!DOCTYPE html>
<html lang="en">
<head>
<meta charset="utf-8">
<title>Hollis Ridge Co. – Business Card</title>
<link href="https://fonts.googleapis.com/css2?family=Orbitron:wght@700;900&family=Roboto+Condensed:wght@700&family=Poppins:wght@500&display=swap" rel="stylesheet">
<style>
  :root {
    --stage: #303030;
    --card-black: #000000;
    --gold: #f9b51a;
    --ink: #111111;
  }
  * { margin: 0; padding: 0; box-sizing: border-box; }
  html, body { width: 1200px; height: 1200px; overflow: hidden; background: var(--stage); }
  .stage { position: relative; width: 1200px; height: 1200px; }

  .card {
    position: absolute;
    top: 303px;
    width: 368px;
    height: 594px;
    background: var(--card-black);
    overflow: hidden;
  }
  .card--front { left: 200px; }
  .card--back { left: 598px; }

  .brand {
    position: absolute;
    left: 0; right: 0;
    display: flex;
    flex-direction: column;
    align-items: center;
    color: var(--gold);
    font-family: "Orbitron", sans-serif;
    font-weight: 700;
  }
  .card--front .brand { top: 62px; }
  .card--back .brand { top: 56px; }

  .brand__mark {
    width: 84px; height: 84px;
    border-radius: 50%;
    background: var(--gold);
    margin-bottom: 34px;
  }
  .brand__name { font-size: 20px; letter-spacing: 1px; line-height: 1; }

  .phone {
    margin-top: 16px;
    font-family: "Poppins", sans-serif; font-weight: 500;
    font-size: 13px; letter-spacing: 2px; line-height: 1;
    color: var(--gold);
  }

  .scene-art {
    position: absolute;
    left: 36px;
    width: 270px;
    background: linear-gradient(to bottom, rgba(249,181,26,0) 0%, rgba(249,181,26,0.55) 45%, var(--gold) 100%);
    border-radius: 120px 120px 0 0;
  }
  .card--front .scene-art { top: 287px; height: 180px; }
  .card--back .scene-art { top: 265px; height: 180px; left: 34px; }

  .accent-line { position: absolute; left: 0; height: 2px; background: var(--gold); }
  .card--front .accent-line { top: 458px; width: 71px; }
  .card--back .accent-line { top: 436px; width: 70px; }

  .info-band {
    position: absolute; left: 0; right: 0; bottom: 0;
    background: var(--gold);
    color: var(--ink);
    display: flex; flex-direction: column; align-items: center;
    padding-top: 27px;
  }
  .card--front .info-band { top: 467px; }
  .card--back .info-band { top: 445px; }

  .info-band__title {
    font-family: "Orbitron", sans-serif; font-weight: 900;
    font-size: 16px; letter-spacing: 0.5px; line-height: 1;
  }
  .info-band__divider { width: 83px; height: 1px; background: var(--ink); margin: 13px 0 12px; }

  .services {
    font-family: "Roboto Condensed", sans-serif; font-weight: 700;
    font-size: 17px; line-height: 1; white-space: nowrap;
  }
  .contact {
    font-family: "Poppins", sans-serif; font-weight: 500;
    font-size: 16px; line-height: 25px; text-align: center; white-space: nowrap;
  }
</style>
</head>
<body>
<main class="stage">

  <section class="card card--front" aria-label="Card front">
    <div class="brand">
      <div class="brand__mark"></div>
      <div class="brand__name">HOLLIS RIDGE CO.</div>
      <div class="phone">555-714-9082</div>
    </div>
    <div class="scene-art" role="img" aria-label="Gold silhouette of palm trees and an excavator on a rise of ground"></div>
    <div class="accent-line"></div>
    <div class="info-band">
      <h2 class="info-band__title">SPECIALIZES IN</h2>
      <div class="info-band__divider"></div>
      <p class="services">LAND CLEARING | MULCHING | EXCAVATION</p>
    </div>
  </section>

  <section class="card card--back" aria-label="Card back">
    <div class="brand">
      <div class="brand__mark"></div>
      <div class="brand__name">HOLLIS RIDGE CO.</div>
      <div class="phone">555-714-9082</div>
    </div>
    <div class="scene-art" role="img" aria-label="Gold silhouette of palm trees and an excavator on a rise of ground"></div>
    <div class="accent-line"></div>
    <div class="info-band">
      <h2 class="info-band__title">DALE VORSKIN</h2>
      <div class="info-band__divider"></div>
      <p class="contact">OFFICE@TRV-GROUNDMAKRZ.COM<br>WWW.TRV-GROUNDMAKRZ.COM</p>
    </div>
  </section>

</main>
</body>
</html>
```